Book Cover

Book cover for a study guide on Corvanians. The title would be: "Corvanians: Unbound to Walk Onward" Possibly using a bird breaking free from a cage.+

Target Market(s)

We will sell them to our church.

Requirements
Must have
• Authors are Dr. Martin Oskeby and Dr. Helena Oskeby

```html
<!DOCTYPE html>
<html lang="en">
<head>
<meta charset="utf-8">
<title>Corvanians: Unbound to Walk Onward – Book Wrap</title>
<link href="https://fonts.googleapis.com/css2?family=Cinzel:wght@400;700&family=Arimo:wght@400;700&display=swap" rel="stylesheet">
<style>
  :root{
    --page:#ffffff;
    --ink:#000000;
    --sun:#fccb5c;
    --gold:#f4cc6e;
    --gold-deep:#e0ad45;
    --dark-text:#0b0b0b;
    --plate:#f4f1f6;
    --lilac:#c98fc8;
  }
  *{box-sizing:border-box;margin:0;padding:0}
  html,body{width:955px;height:1200px;overflow:hidden;background:var(--page)}
  .canvas{position:relative;width:955px;height:1200px;overflow:hidden}
  .wrap{position:absolute;left:20px;top:320px;width:1433px;height:878px;transform:scale(0.6385);transform-origin:0 0}
  .panel{position:absolute;top:0;height:878px;background:var(--sun);padding:11px}
  .panel-inner{position:relative;width:100%;height:100%;background:var(--ink);overflow:hidden}
  .back{left:0;width:616px}
  .spine{left:629px;width:174px}
  .front{left:818px;width:615px}

  .art{position:absolute;border-radius:6px}
  .birds{background:linear-gradient(90deg,rgba(244,204,110,.55),rgba(244,204,110,.25))}

  .serif{font-family:'Cinzel',serif;color:var(--gold)}
  .sans{font-family:'Arimo',Arial,sans-serif}

  /* back */
  .back .birds{left:170px;top:45px;width:230px;height:90px}
  .back-title{position:absolute;left:0;right:0;top:118px;text-align:center;font-size:36px;letter-spacing:1px;padding-left:40px}
  .back-subtitle{position:absolute;left:0;right:0;top:162px;text-align:center;font-size:12.5px;letter-spacing:1.5px;padding-left:40px}
  .bio-label{position:absolute;left:46px;font-family:'Cinzel',serif;font-weight:700;font-size:12px;color:var(--gold)}
  .bio-name{position:absolute;left:46px;font-size:25px}
  .bio-text{position:absolute;left:62px;width:480px}
  .bio-text p{font-family:'Arimo',Arial,sans-serif;font-size:6.6px;line-height:9.3px;color:var(--gold);margin-bottom:12px;white-space:pre-line}
  .signature-label{position:absolute;left:432px;top:758px;font-family:'Cinzel',serif;font-size:11px;font-style:italic;color:var(--gold)}
  .signature-box{position:absolute;left:390px;top:767px;width:141px;height:63px;background:var(--sun)}

  /* spine */
  .spine-block{position:absolute;left:0;width:152px}
  .spine-birds{position:absolute;left:70px;width:50px;height:140px}
  .vertical{position:absolute;transform-origin:0 0;transform:rotate(90deg);white-space:nowrap}
  .spine-title{font-size:26px;letter-spacing:1px}
  .spine-sub{font-size:7.5px;letter-spacing:.8px}
  .spine-authors{font-size:26px;line-height:26px}
  .spine-by{font-family:'Arimo',Arial,sans-serif;font-weight:700;font-size:9px;color:var(--gold)}

  /* front */
  .front .birds{left:240px;top:30px;width:200px;height:80px}
  .front-title{position:absolute;left:0;right:0;top:104px;text-align:center;font-size:84px;letter-spacing:1px;color:var(--gold)}
  .front-subtitle{position:absolute;left:0;right:0;top:200px;text-align:center;font-size:32px;letter-spacing:1.5px}
  .ground{position:absolute;left:0;top:0;width:593px;height:856px}
  .scene{left:100px;top:235px;width:430px;height:440px;border-radius:40% 40% 50% 50%;
    background:radial-gradient(ellipse at 50% 72%,var(--plate) 0 42%,rgba(201,143,200,.55) 60%,rgba(244,204,110,.35) 78%,rgba(0,0,0,0) 100%)}
  .authors{position:absolute;left:0;right:0;top:734px;text-align:center;color:var(--dark-text)}
  .authors-by{font-family:'Arimo',Arial,sans-serif;font-weight:700;font-size:12px;margin-bottom:9px}
  .author{font-family:'Cinzel',serif;font-weight:700;font-size:27px;line-height:24px}
  .amp{font-family:'Cinzel',serif;font-weight:700;font-size:22px;line-height:18px}
</style>
</head>
<body>
<main class="canvas">
  <div class="wrap">

    <!-- back cover -->
    <section class="panel back">
      <div class="panel-inner">
        <div class="art birds" role="img" aria-label="Gold birds in flight with small clouds"></div>
        <div class="back-title serif">CORVANIANS</div>
        <div class="back-subtitle serif">UNBOUND TO WALK ONWARD</div>

        <div class="bio-label" style="top:203px">BIOGRAFHY</div>
        <div class="bio-name serif" style="top:216px">Dr. Martin Oskeby</div>
        <div class="bio-text" style="top:255px">
          <p>Book cover for a study guide on Corvanians. The title would be: "Corvanians: Unbound to Walk Onward" Possibly using a bird breaking free from a cage.+
Book cover for a study guide on Corvanians. The title would be: "Corvanians: Unbound to Walk Onward" Possibly using a bird breaking free from a cage.+
Book cover for a study guide on Corvanians. The title would be: "Corvanians: Unbound to Walk Onward" Possibly using a bird breaking free from a cage.+
Book cover for a study guide on Corvanians. The title would be: "Corvanians: Unbound to Walk Onward" Possibly using a bird breaking free from a cage.+
Book cover for a study guide on Corvanians. The title would be: "Corvanians: Unbound to Walk Onward" Possibly using a bird breaking free from a cage.+
Book cover for a study guide on Corvanians. The title would be: "Corvanians: Unbound to Walk Onward" Possibly using a bird breaking free from a cage.+</p>
          <p>Book cover for a study guide on Corvanians. The title would be: "Corvanians: Unbound to Walk Onward" Possibly using a bird breaking free from a cage.+
Book cover for a study guide on Corvanians. The title would be: "Corvanians: Unbound to Walk Onward" Possibly using a bird breaking free from a cage.+
Book cover for a study guide on Corvanians. The title would be: "Corvanians: Unbound to Walk Onward" Possibly using a bird breaking free from a cage.+
Book cover for a study guide on Corvanians. The title would be: "Corvanians: Unbound to Walk Onward" Possibly using a bird breaking free from a cage.+
Book cover for a study guide on Corvanians. The title would be: "Corvanians: Unbound to Walk Onward" Possibly using a bird breaking free from a cage.+
Book cover for a study guide on Corvanians. The title would be: "Corvanians: Unbound to Walk Onward" Possibly using a bird breaking free from a cage.+</p>
          <p>Book cover for a study guide on Corvanians. The title would be: "Corvanians: Unbound to Walk Onward" Possibly using a bird breaking free from a cage.+
Book cover for a study guide on Corvanians. The title would be: "Corvanians: Unbound to Walk Onward" Possibly using a bird breaking free from a cage.+
Book cover for a study guide on Corvanians. The title would be: "Corvanians: Unbound to Walk Onward" Possibly using a bird breaking free from a cage.+
Book cover for a study guide on Corvanians. The title would be: "Corvanians: Unbound to Walk Onward" Possibly using a bird breaking free from a cage.+
Book cover for a study guide on Corvanians. The title would be: "Corvanians: Unbound to Walk Onward" Possibly using a bird breaking free from a cage.+
Book cover for a study guide on Corvanians. The title would be: "Corvanians: Unbound to Walk Onward" Possibly using a bird breaking free from a cage.+</p>
        </div>

        <div class="bio-label" style="top:475px">BIOGRAFHY</div>
        <div class="bio-name serif" style="top:490px">Dr. Helena Oskeby</div>
        <div class="bio-text" style="top:540px">
          <p>Book cover for a study guide on Corvanians. The title would be: "Corvanians: Unbound to Walk Onward" Possibly using a bird breaking free from a cage.+
Book cover for a study guide on Corvanians. The title would be: "Corvanians: Unbound to Walk Onward" Possibly using a bird breaking free from a cage.+
Book cover for a study guide on Corvanians. The title would be: "Corvanians: Unbound to Walk Onward" Possibly using a bird breaking free from a cage.+
Book cover for a study guide on Corvanians. The title would be: "Corvanians: Unbound to Walk Onward" Possibly using a bird breaking free from a cage.+
Book cover for a study guide on Corvanians. The title would be: "Corvanians: Unbound to Walk Onward" Possibly using a bird breaking free from a cage.+
Book cover for a study guide on Corvanians. The title would be: "Corvanians: Unbound to Walk Onward" Possibly using a bird breaking free from a cage.+</p>
          <p>Book cover for a study guide on Corvanians. The title would be: "Corvanians: Unbound to Walk Onward" Possibly using a bird breaking free from a cage.+
Book cover for a study guide on Corvanians. The title would be: "Corvanians: Unbound to Walk Onward" Possibly using a bird breaking free from a cage.+
Book cover for a study guide on Corvanians. The title would be: "Corvanians: Unbound to Walk Onward" Possibly using a bird breaking free from a cage.+
Book cover for a study guide on Corvanians. The title would be: "Corvanians: Unbound to Walk Onward" Possibly using a bird breaking free from a cage.+
Book cover for a study guide on Corvanians. The title would be: "Corvanians: Unbound to Walk Onward" Possibly using a bird breaking free from a cage.+
Book cover for a study guide on Corvanians. The title would be: "Corvanians: Unbound to Walk Onward" Possibly using a bird breaking free from a cage.+</p>
          <p>Book cover for a study guide on Corvanians. The title would be: "Corvanians: Unbound to Walk Onward" Possibly using a bird breaking free from a cage.+
Book cover for a study guide on Corvanians. The title would be: "Corvanians: Unbound to Walk Onward" Possibly using a bird breaking free from a cage.+
Book cover for a study guide on Corvanians. The title would be: "Corvanians: Unbound to Walk Onward" Possibly using a bird breaking free from a cage.+
Book cover for a study guide on Corvanians. The title would be: "Corvanians: Unbound to Walk Onward" Possibly using a bird breaking free from a cage.+
Book cover for a study guide on Corvanians. The title would be: "Corvanians: Unbound to Walk Onward" Possibly using a bird breaking free from a cage.+
Book cover for a study guide on Corvanians. The title would be: "Corvanians: Unbound to Walk Onward" Possibly using a bird breaking free from a cage.+</p>
        </div>

        <div class="signature-label">Signature</div>
        <div class="signature-box"></div>
      </div>
    </section>

    <!-- spine -->
    <section class="panel spine">
      <div class="panel-inner">
        <div class="art birds spine-birds" style="top:65px" role="img" aria-label="Gold birds in flight"></div>
        <div class="vertical serif spine-title" style="left:82px;top:85px">CORVANIANS</div>
        <div class="vertical serif spine-sub" style="left:50px;top:105px">UNBOUND TO WALK ONWARD</div>

        <div class="vertical spine-by" style="left:126px;top:400px">Authors By :</div>
        <div class="vertical serif spine-authors" style="left:108px;top:315px;text-align:center">Dr. Martin Oskeby<br>&amp;<br>Dr. Helena Oskeby</div>

        <div class="art birds spine-birds" style="top:625px" role="img" aria-label="Gold birds in flight"></div>
        <div class="vertical serif spine-title" style="left:82px;top:645px">CORVANIANS</div>
        <div class="vertical serif spine-sub" style="left:50px;top:665px">UNBOUND TO WALK ONWARD</div>
      </div>
    </section>

    <!-- front cover -->
    <section class="panel front">
      <div class="panel-inner">
        <svg class="ground" viewBox="0 0 593 856" aria-hidden="true">
          <path d="M0 600 C0 690 60 740 150 735 C 260 728 330 690 360 600 C 385 520 450 475 520 472 C 560 470 585 490 593 515 L593 856 L0 856 Z" fill="var(--sun)"/>
        </svg>
        <div class="art birds" role="img" aria-label="Gold birds flying upward"></div>
        <div class="front-title serif">CORVANIANS</div>
        <div class="front-subtitle serif">UNBOUND TO WALK ONWARD</div>
        <div class="art scene" role="img" aria-label="Illustration of an open gold birdcage on a white plate with pink flowers, a bird flying out toward a yellow sun"></div>
        <div class="authors">
          <div class="authors-by">Authors By :</div>
          <div class="author">Dr. Martin Oskeby</div>
          <div class="amp">&amp;</div>
          <div class="author">Dr. Helena Oskeby</div>
        </div>
      </div>
    </section>

  </div>
</main>
</body>
</html>
```